eBook Cover_H. Lindqvist-Borna
Schnell und zuverlässoig,Änderungswünsche wurden umgehend ausgeführt. Vielen Dank für das tolle Cover zu meinem ersten Buch!
Zielgruppe
freie Roman-Autorin (Erstlingswerk)
Zielgruppe: Lesende (Erwachsene), Frauen
Charakterisierung: magisch-realistischer Familienroman, spielt im Europa der Jetzt-Zeit
Aufgabenstellung
Im ersten Schritt geht es um ein Cover für ein eBook, das aber bei Bedarf als Book on Demand gedruckt werden soll. Es wird daher später Anforderung bzgl. Dicke / Umfang des gedruckten Buches und einer Rückseite geben. Das gewählte Design soll dann dahingehend überarbeitet und finale Druckdaten zur Verfügung gestellt werden. Dies soll von vornherein berücksichtigt werden und im Preis enthalten sein.
Titel: Regen über Glas, Monde im Moos
Autorinnenname: Henrike Lindqvist-Borna
des weiteren auf dem Cover: Roman

```html
<!DOCTYPE html>
<html lang="de">
<head>
<meta charset="utf-8">
<title>Regen über Glas, Monde im Moos – Henrike Lindqvist-Borna</title>
<link rel="stylesheet" href="https://fonts.googleapis.com/css2?family=Open+Sans:wght@400&family=Oswald:wght@600&display=swap">
<style>
  :root {
    --backdrop: #dcdcdc;
    --paper: #ffffff;
    --ink: #5a6169;
    --label: #ffffff;
    --sky: #3b3fb0;
    --haze: #4a6a8a;
    --meadow: #8fc23a;
    --field: #c9c23a;
    --poppy: #d8281c;
  }
  * { margin: 0; padding: 0; box-sizing: border-box; }
  html, body {
    width: 841px;
    height: 1200px;
    overflow: hidden;
    background: var(--backdrop);
  }
  .cover {
    position: absolute;
    left: 45px;
    top: 45px;
    width: 750px;
    height: 1108px;
    background: var(--paper);
    box-shadow: 6px 6px 6px rgba(0, 0, 0, 0.35);
    overflow: hidden;
  }
  .cover__author {
    position: absolute;
    top: 176px;
    left: 0;
    width: 100%;
    text-align: center;
    font-family: "Open Sans", Arial, sans-serif;
    font-size: 25px;
    font-weight: 400;
    letter-spacing: 0.3px;
    color: var(--ink);
  }
  .cover__rule {
    position: absolute;
    top: 216px;
    left: 272px;
    width: 204px;
    height: 5px;
    background: var(--ink);
  }
  .cover__title {
    position: absolute;
    top: 280px;
    left: 0;
    width: 100%;
    text-align: center;
    font-family: "Oswald", "Arial Narrow", sans-serif;
    font-weight: 600;
    font-size: 70px;
    line-height: 72px;
    letter-spacing: 1.5px;
    color: var(--ink);
    text-transform: uppercase;
  }
  .cover__artwork {
    position: absolute;
    left: 0;
    top: 626px;
    width: 750px;
    height: 482px;
    display: block;
  }
  .cover__genre {
    position: absolute;
    top: 786px;
    left: 0;
    width: 100%;
    text-align: center;
    font-family: "Oswald", "Arial Narrow", sans-serif;
    font-weight: 600;
    font-size: 60px;
    line-height: 72px;
    letter-spacing: 1px;
    color: var(--label);
  }
</style>
</head>
<body>
  <main class="cover">
    <p class="cover__author">HENRIKE LINDQVIST-BORNA</p>
    <div class="cover__rule"></div>
    <h1 class="cover__title">Regen über Glas<br>Monde im Moos</h1>

    <svg class="cover__artwork" viewBox="0 0 750 482" role="img" aria-label="Gemalte Landschaft: blauer Himmel über einer grün-gelben Wiese mit roten Mohnblumen">
      <defs>
        <linearGradient id="landscape" x1="0" y1="0" x2="0" y2="1">
          <stop offset="0" stop-color="var(--sky)"/>
          <stop offset="0.18" stop-color="var(--haze)"/>
          <stop offset="0.32" stop-color="var(--meadow)"/>
          <stop offset="0.6" stop-color="var(--field)"/>
          <stop offset="0.8" stop-color="#9bbd30"/>
          <stop offset="1" stop-color="#b04a20"/>
        </linearGradient>
        <linearGradient id="blooms" x1="0" y1="0" x2="0" y2="1">
          <stop offset="0.3" stop-color="var(--poppy)" stop-opacity="0"/>
          <stop offset="0.75" stop-color="var(--poppy)" stop-opacity="0.25"/>
          <stop offset="1" stop-color="var(--poppy)" stop-opacity="0.55"/>
        </linearGradient>
      </defs>
      <polygon points="0,0 375,80 750,0 750,482 0,482" fill="url(#landscape)"/>
      <polygon points="0,0 375,80 750,0 750,482 0,482" fill="url(#blooms)"/>
    </svg>

    <p class="cover__genre">ROMAN</p>
  </main>
</body>
</html>
```